Modern Business Card

Modern professional business card with more than just logo and demographic info. Something memorable.

We are a trendy/modern chiropractic group with an emphasis on neurology, hence the minimalist-type brain logo. We want to convey that modern and technical aspect with professionalism and the elite nature of our practice environment.

```html
<!DOCTYPE html>
<html lang="en">
<head>
<meta charset="utf-8">
<title>Meridian Chiropractic – Business Card</title>
<link rel="stylesheet" href="https://fonts.googleapis.com/css2?family=Tinos&family=Zilla+Slab:wght@700&family=Arimo&display=swap">
<style>
  :root {
    --page-bg: #d9dadc;
    --card-dark: #050607;
    --card-light: #ffffff;
    --brand-blue: #3f7cc6;
    --ink: #161616;
    --ink-soft: #2a2a2a;
    --rule: #c9c9c9;
  }
  * { box-sizing: border-box; margin: 0; padding: 0; }
  html, body { width: 1200px; height: 1200px; overflow: hidden; }
  body {
    background: var(--page-bg);
    display: flex;
    flex-direction: column;
    align-items: center;
    justify-content: center;
    gap: 56px;
  }
  .card {
    width: 840px;
    height: 480px;
    box-shadow: 0 10px 28px rgba(0,0,0,0.25);
    position: relative;
  }
  .card--front {
    background: var(--card-dark);
    border-radius: 110px 0 110px 0;
    display: flex;
    align-items: center;
    justify-content: center;
  }
  .card--back {
    background: var(--card-light);
    border-radius: 0 110px 0 110px;
    display: flex;
    align-items: center;
  }
  .brand {
    display: flex;
    align-items: center;
    gap: 22px;
  }
  .brand__mark {
    width: 34px;
    height: 34px;
    background: var(--brand-blue);
    flex: none;
  }
  .brand__name {
    font-family: "Tinos", serif;
    font-weight: 400;
    text-transform: uppercase;
    line-height: 1.02;
    letter-spacing: 1px;
  }
  .card--front .brand__name { color: #ffffff; font-size: 50px; }
  .card--back .brand__name { color: var(--ink); font-size: 38px; }

  .card__brand-side {
    width: 50%;
    display: flex;
    justify-content: center;
  }
  .card--back .brand { flex-direction: column; gap: 18px; text-align: center; }
  .card--back .brand__mark { width: 46px; height: 46px; }

  .card__divider {
    width: 2px;
    height: 250px;
    background: var(--rule);
  }
  .contact {
    padding-left: 44px;
    font-family: "Arimo", sans-serif;
    color: var(--ink);
  }
  .contact__name {
    font-family: "Zilla Slab", serif;
    font-weight: 700;
    color: var(--brand-blue);
    font-size: 30px;
    letter-spacing: 1px;
    text-transform: uppercase;
    line-height: 1;
  }
  .contact__role {
    font-size: 24px;
    color: var(--ink-soft);
    margin: 2px 0 18px;
  }
  .contact__list { list-style: none; }
  .contact__item {
    display: flex;
    align-items: center;
    gap: 10px;
    font-size: 24px;
    line-height: 1.25;
  }
  .contact__icon { width: 24px; height: 24px; flex: none; }
  .contact__link-accent { color: var(--brand-blue); }
  .contact__address {
    font-size: 24px;
    line-height: 1.2;
    margin-top: 18px;
    font-style: normal;
  }
</style>
</head>
<body>

  <section class="card card--front" aria-label="Card front">
    <div class="brand">
      <span class="brand__mark"></span>
      <p class="brand__name">Meridian<br>Chiropractic</p>
    </div>
  </section>

  <section class="card card--back" aria-label="Card back">
    <div class="card__brand-side">
      <div class="brand">
        <span class="brand__mark"></span>
        <p class="brand__name">Meridian<br>Chiropractic</p>
      </div>
    </div>
    <div class="card__divider"></div>
    <div class="contact">
      <h1 class="contact__name">Daniel Whitford</h1>
      <p class="contact__role">Managing Director</p>
      <ul class="contact__list">
        <li class="contact__item">
          <svg class="contact__icon" viewBox="0 0 24 24" aria-hidden="true">
            <rect x="2" y="2" width="20" height="20" rx="4" fill="none" stroke="#3f7cc6" stroke-width="2"/>
            <path d="M8 6c-1 1-1 3 1 6s4 5 6 5l1.5-1.5-2.5-2-1.2 1c-1.2-.6-2.6-2-3.2-3.2l1-1.2-2-2.5z" fill="#3f7cc6"/>
          </svg>
          <span>071-386 902 417</span>
        </li>
        <li class="contact__item">
          <svg class="contact__icon" viewBox="0 0 24 24" aria-hidden="true">
            <rect x="2" y="5" width="20" height="14" fill="#3f7cc6"/>
            <path d="M2 5l10 8 10-8" fill="none" stroke="#fff" stroke-width="1.6"/>
          </svg>
          <span>info@meridianchiro.com</span>
        </li>
        <li class="contact__item">
          <svg class="contact__icon" viewBox="0 0 24 24" aria-hidden="true">
            <g fill="none" stroke="#3f7cc6" stroke-width="1.8">
              <circle cx="12" cy="12" r="9.5"/>
              <ellipse cx="12" cy="12" rx="4" ry="9.5"/>
              <path d="M2.5 12h19M4 7h16M4 17h16"/>
            </g>
          </svg>
          <span>www.<span class="contact__link-accent">meridianchiro</span>.com</span>
        </li>
      </ul>
      <address class="contact__address">87, Harbor Lane West<br>Eastfield, 60318</address>
    </div>
  </section>

</body>
</html>
```